New Business Card for Software Company

We are looking at rebranding a 10 year old company that specializes in PDF and DWF solutions for Architects and Engineers. We will attach the new company logo that we are going with so you can work with that and complimentary colors.
The sample information we would like on the business card is:
Gerald Pinfold
Vice President
4738 W. Harrowgate Lane. STE 305
PMB#417
Dunmore Ridge, CO 85374
866-392-5074 US Toll Free
123-456-3190 Cell
gpinfold@plavorix.com
The old tag line that we had on the business cars was.
Delivering Dependable PDF and DWF Tools to Architects and Engineers Worldwide.
If you have an idea for a better tag line we are open to that also.
Updates
We would like to thank all of the Designers for their wonderful work. We apologize that we will not have the time to provide feedback to everyone. There is just so many innovative and professional designs that you have all created making our decision even harder.
Target Market(s)
Architects and Engineers
Industry/Entity Type
Business
Look and feel

```html
<!DOCTYPE html>
<html lang="en">
<head>
<meta charset="utf-8">
<title>Plavorix Business Card</title>
<link href="https://fonts.googleapis.com/css2?family=Arimo:wght@400;700&family=Open+Sans:wght@400;600&display=swap" rel="stylesheet">
<style>
  :root {
    --stage: #e6e5ec;
    --card: #ffffff;
    --orange: #e8561f;
    --orange-light: #f39321;
    --red: #cf2630;
    --grey-text: #5f5f5f;
    --grey-dark: #555555;
    --rule: #b8b8b8;
    --shadow: rgba(60, 60, 80, 0.18);
  }
  * { box-sizing: border-box; margin: 0; padding: 0; }
  html, body {
    width: 1200px; height: 987px; overflow: hidden;
    background: var(--stage);
  }
  .stage { position: relative; width: 1200px; height: 987px; }

  .card {
    position: absolute;
    width: 680px; height: 390px;
    background: var(--card);
    border-radius: 34px;
    box-shadow: 0 14px 30px var(--shadow);
    overflow: hidden;
  }

  /* Back of card */
  .card--back { left: 470px; top: 50px; }
  .card--back .brand-name {
    position: absolute; left: 70px; top: 95px;
    font-family: "Arimo", Arial, sans-serif;
    font-weight: 700; font-size: 110px; letter-spacing: -3px;
    color: var(--grey-dark); line-height: 1;
  }
  .card--back .tagline {
    position: absolute; left: 75px; top: 235px; width: 560px;
    font-family: "Open Sans", Arial, sans-serif;
    font-size: 22px; line-height: 1.3; color: var(--grey-text);
  }

  /* Front of card */
  .card--front { left: 50px; top: 510px; }
  .brand {
    position: absolute; left: 40px; top: 34px;
    display: flex; align-items: center; gap: 16px;
  }
  .brand-mark {
    width: 62px; height: 62px; border-radius: 50%;
    background: var(--orange);
  }
  .card--front .brand-name {
    font-family: "Arimo", Arial, sans-serif;
    font-weight: 700; font-size: 68px; letter-spacing: -2px;
    color: var(--orange); line-height: 1;
  }
  .person {
    position: absolute; left: 44px; top: 128px;
    font-family: "Arimo", Arial, sans-serif;
  }
  .person-name { font-weight: 700; font-size: 28px; color: var(--orange); }
  .person-title { font-size: 22px; color: var(--grey-text); margin-left: 6px; }
  .contacts {
    position: absolute; left: 50px; top: 176px; list-style: none;
    font-family: "Arimo", Arial, sans-serif; font-size: 20px; color: var(--grey-text);
  }
  .contacts li { display: flex; align-items: center; gap: 10px; height: 32px; }
  .contacts svg { width: 16px; height: 16px; fill: var(--orange); flex: none; }

  .band { position: absolute; left: 0; bottom: 0; width: 680px; height: 100px; }
  .address {
    position: absolute; left: 30px; bottom: 22px;
    font-family: "Arimo", Arial, sans-serif; font-size: 18px; color: #ffffff;
    white-space: nowrap;
  }
</style>
</head>
<body>
<main class="stage">

  <section class="card card--back" aria-label="Card back">
    <div class="brand-name">plavorix</div>
    <p class="tagline">Delivering Dependable PDF and DWF Tools<br>to Architects and Engineers Worldwide</p>
  </section>

  <section class="card card--front" aria-label="Card front">
    <div class="brand">
      <span class="brand-mark"></span>
      <span class="brand-name">plavorix</span>
    </div>

    <p class="person">
      <span class="person-name">Gerald Pinfold,</span><span class="person-title">Vice President</span>
    </p>

    <ul class="contacts">
      <li>
        <svg viewBox="0 0 16 16" aria-hidden="true"><path d="M3.5 1l2.5 3-1.5 2c1 2 3 4 5 5l2-1.5 3 2.5-1.5 2.5C7 14 2 9 1 2.5z"/></svg>
        866-392-5074(US) TF
      </li>
      <li>
        <svg viewBox="0 0 16 16" aria-hidden="true"><rect x="4" y="1" width="8" height="14" rx="1.5"/><rect x="5.5" y="3" width="5" height="6" fill="#fff"/></svg>
        123-456-3190
      </li>
      <li>
        <svg viewBox="0 0 16 16" aria-hidden="true"><rect x="1" y="3" width="14" height="10" rx="1.5"/><path d="M2 4l6 5 6-5" stroke="#fff" stroke-width="1.4" fill="none"/></svg>
        gpinfold@plavorix.com
      </li>
    </ul>

    <svg class="band" viewBox="0 0 680 100" preserveAspectRatio="none" aria-hidden="true">
      <defs>
        <linearGradient id="bandGradient" x1="0" y1="0" x2="1" y2="0">
          <stop offset="0" stop-color="#cf2630"/>
          <stop offset="0.55" stop-color="#e8561f"/>
          <stop offset="1" stop-color="#f39321"/>
        </linearGradient>
      </defs>
      <path d="M0 30 H560 C610 30 630 0 680 0 V100 H0 Z" fill="url(#bandGradient)"/>
      <path d="M0 26 H560 C610 26 630 -4 680 -4" stroke="#b8b8b8" stroke-width="1.5" fill="none"/>
    </svg>
    <p class="address">4738 W. Harrowgate Lane. STE 305, PMB#417, Dunmore Ridge, CO 85374</p>
  </section>

</main>
</body>
</html>
```